SaaS / Consulting / Solution website redesign

We need a website design that:
- Is completely different than our current design : https://plumvessel.net
- Has a very minimal amount of copy
- Changes our positioning from a SaaS application to a solutions company. Solutions company means that we help our customers solve their problems with consulting, training, and tools. An example of a solutions company is here: https://oldpages.example/web/20130111103320/http://www.brindlework.com:80/
- Does not make us look like a start up
- Is more people oriented than technology oriented

We need a designer that:
- Is a rebel at heart
- Is a minimalist
- Tells us why our current site sucks
- Can disagree with us
- Can also do copywriting or already has a copywriter that can help
- Is ok with saying we have capability that we don't in order to see if people actually want that
- Can understand the difference between our grand vision and where we need to focus ourselves today in order to get there

Who we are:
- Entrepreneurs
- Programmers
- Consultants
- Investors

Here's our design goals:
#1 Get customers, investors, employers, and partners excited about our unique and clearly articulated value proposition
#2 Get people to contact us asking for help with their programs
#3 Position ourselves as an expert in the skills based volunteering, mentorship, and group collaboration
#4 Make it easy for people, who already know who we are, to register online

What our grand vision is:
- Create a marketplace where any person can go to our site and find time with anyone they need to meet with. Whether that is their hair stylist, school advisor, parent of your kids class, dentist, attorney, etc.

What will you get if you win:
- In addition to the prize of this project we will have many landing pages and other revisions we will need in the future. We currently don't have a designer or copywriter and need to add that capability to our team

Who do we need to appeal to:
- Directors that are launching innovative programs inside organizations
- IT personnel who are trying to disqualify our technology so they don't have to support it or deal with it when it doesn't go well
- Enterprise IT architects who don't want our product being on its own island within their organization totally incompatible with everything else. Architects which are trying to assess how our platform will co-exist with all their other platforms
- Vice Presidents who want to help their directors understand that we don't have enough experience to help them
- Program managers who have to juggle a million things and need a tool that actually helps instead of confuses them and adds more work for them.
- Program managers & directors that have been given ambiguous goals by their board of directors like "improve retention, increase engagement, create innovation, get people to collaborate." And who have no idea where to start or how to deliver on things like that.
- Program managers, directors, and vice presidents that are trying to understand how our technology and services fit into their existing technology and capability
- Employees who are bored and uninspired with their current tools and are hoping for some excitement in their life. Kind of like candy or a double espresso.
- Investors who think, our company like all the rest, are going to waste their money and make them look like a fool

Other information:
-The CSS and html needs to be responsive

-Our registration onboarding flow needs to collect this information:
User first name
user last name
user email
(verify their email)
user phone number
(verify their phone number)
User profile image (optional)
User profile summary (optional, like a bio, freeform text fiels)
If applicable: Register their organization
Organization name
Organization image (optional)
Account Mailing address
account Billing address (could be same as mailing address)
account Billing email address (could be same as user address)
account Product selection (pricing tier)
account Credit card information

The designs I am getting are a good start but they are only the front page. I just want you to know that I am expecting and need more than a landing page to complete the design. I will likely need a page that outlines the benefits and features of the product itself, how its different than our competitors, which will not be on the front page. I will need a registration flow. I will need a blog page design so we can post blog articles, I will need a team page, a page that goes into detail on our training, our services. I will likely need a page that shows all news and media we have been in. I need to show customer and user quotes, case studies, a way to contact us, partners, general resources like on collaboration, product tutorials, customers. I need the site to address a comprehensive set of needs. I need that design to be consistent and thorough. I know what PlateHarbor is. I'm not using because I need more than a template that was customized. I need to be unique and match our brand thoughtfully, beautifully, and artistically. Someone asked me a question about how Murmly is similar to our tool in the way it is referred by end users and purchased by managers. Our website needs to primarily talk to the managers as I explained in the brief but it needs to appear cool and exciting to our end-users without focusing on the technology too much. Murmly is a tool that teams use to collaborate in small and large enterprises. The value prop for them is that communication is easier. But they don't put that on their website. Why? Because the users of the technology won't go to the website to find out information on it, they get their information from someone who is using it and demos it to them. When Ines tells her manager Otto "Lets get murmly, Ruth is using it at her company and its great" Ines's manager doesn't know anything about murmly so she promptly googles it. The most important thing from Ines's perspective is that Otto agrees to try it out. Otto's biggest concern is that productivity will be enhanced to degraded. Murmly knows this and so on the front page they know they are talking to Otto NOT Ines because Ines is already sold on it and doesn't need to get sold on the website. Ines is end user. Otto is the purchaser. We have the same problem and so our end users are not the ones purchasing our product, their managers are purchasing our product. We get referred by our end users and vetted by their managers. Hope this helps! Thank you for looking at this project!  Added Wednesday, June 7, 2017

Another observation I am having about the designs being submitted. I believe we used the animations on our current website because animations / cartoons connect with the "inner child" in our users. Whatever that means :-). I think it's what makes our brand fun. I have a hard time imagining that we could make the design fun looking without animations but I'm sure it can be achieved. I also recognize that blending pictures of real people and animations is hard. So either we must masterfully blend them, use only animations, or make the real people have a LOT of fun! So far most of the designs while achieve the goal of appealing to the serious Vice Presidents and directors, they are not doing a good job at appealing to the overworked program managers and bored employees. There seems to stand another challenge with animations which is animations are hard to find and/or create that achieve the message / emotion we are trying to communicate. I don't have any good answers for this but I will say we can hire both animators and illustrators if we need to. All you have to do is communicate the effect in the website design with some simpler version maybe not the end illustration or animation itself. Added Wednesday, June 7, 2017

• Sex appeal and a sense of humor. Copy that makes people excited and clairvoyant about our potential.
• Boring renditions of other non-inspiring websites

```html
<!DOCTYPE html>
<html lang="en">
<head>
<meta charset="utf-8">
<title>Registration – Verify your Email</title>
<link rel="stylesheet" href="https://fonts.googleapis.com/css2?family=Fredoka:wght@500&family=Montserrat:wght@400;500&display=swap">
<style>
  :root {
    --sky: #3fb1e7;
    --brand-blue: #3aa9e1;
    --card: #ffffff;
    --ground: #eef1f0;
    --text-muted: #5b6a73;
    --placeholder: #a3acb2;
    --rule: #d9dee1;
    --accent-green: #8fcf6e;
    --white: #ffffff;
  }
  * { box-sizing: border-box; margin: 0; padding: 0; }
  html, body { width: 1200px; height: 725px; overflow: hidden; }
  body {
    background: var(--sky);
    font-family: "Montserrat", Arial, sans-serif;
    position: relative;
  }

  .topbar {
    position: absolute; top: 18px; right: 82px;
    display: flex; align-items: center; gap: 14px;
    color: var(--white); font-size: 13.5px; font-weight: 500;
  }
  .close-button {
    width: 32px; height: 32px; border-radius: 50%;
    background: var(--accent-green); border: 2px solid rgba(255,255,255,.85);
    display: flex; align-items: center; justify-content: center;
  }

  .ground {
    position: absolute; left: 154px; top: 559px;
    width: 892px; height: 34px; border-radius: 50%;
    background: var(--ground);
  }

  .card {
    position: absolute; left: 229px; top: 152px;
    width: 741px; height: 419px;
    background: var(--card);
    text-align: center;
  }
  .card-title {
    margin-top: 49px;
    font-family: "Fredoka", "Trebuchet MS", sans-serif;
    font-weight: 500; font-size: 27px; color: var(--brand-blue);
  }
  .card-subtitle {
    margin-top: 5px; font-size: 15px; color: var(--text-muted);
  }

  .field {
    position: absolute; left: 205px; width: 330px;
    border-bottom: 1px solid var(--rule);
    display: flex; align-items: center;
    height: 40px; padding: 0 24px;
  }
  .field input {
    border: 0; outline: 0; background: transparent; flex: 1;
    font-family: inherit; font-size: 13px; color: var(--text-muted);
  }
  .field input::placeholder { color: var(--placeholder); }
  .field-email { top: 132px; }
  .field-code { top: 214px; }
  .field-chevron { color: var(--placeholder); font-size: 14px; }

  .step-nav {
    position: absolute; left: 326px; top: 346px;
    display: flex; gap: 9px;
  }
  .step-button {
    width: 41px; height: 41px; border-radius: 50%;
    border: 1.5px solid var(--brand-blue); background: var(--white);
    display: flex; align-items: center; justify-content: center;
  }

  .illustration { position: absolute; border-radius: 40px 40px 8px 8px; }
  .illustration-left {
    left: 174px; top: 278px; width: 140px; height: 293px;
    background: linear-gradient(180deg, #d9712f 0%, #f3b98a 30%, #e8506b 55%, #5fa6a0 75%, #f08a2c 100%);
  }
  .illustration-right {
    left: 880px; top: 354px; width: 158px; height: 217px;
    background: linear-gradient(180deg, #f2a23a 0%, #2f4a5e 25%, #a9b8b4 55%, #e9574a 85%, #b7dcc3 100%);
  }

  .progress {
    position: absolute; left: 205px; top: 660px;
    width: 789px; height: 1px; background: rgba(255,255,255,.85);
  }
  .progress-dot {
    position: absolute; top: -3px; width: 7px; height: 7px;
    border-radius: 50%; background: var(--white); transform: translateX(-50%);
  }
  .progress-dot.is-current {
    top: -6px; width: 13px; height: 13px;
    background: var(--accent-green); border: 2px solid var(--white);
  }
</style>
</head>
<body>

<header class="topbar">
  <span class="topbar-label">Registration</span>
  <span class="close-button" aria-label="Close">
    <svg width="10" height="10" viewBox="0 0 10 10"><path d="M1 1l8 8M9 1l-8 8" stroke="#fff" stroke-width="1.6" stroke-linecap="round"/></svg>
  </span>
</header>

<div class="ground"></div>

<main class="card">
  <h1 class="card-title">Verify your Email</h1>
  <p class="card-subtitle">Keeping our members safe starts with verifying their information</p>

  <label class="field field-email">
    <input type="email" placeholder="Type your Email ...">
    <span class="field-chevron">›</span>
  </label>
  <label class="field field-code">
    <input type="text" placeholder="Enter Code ...">
  </label>

  <nav class="step-nav">
    <span class="step-button" aria-label="Previous step">
      <svg width="18" height="14" viewBox="0 0 18 14"><path d="M17 7H2M7 1.5L1.5 7 7 12.5" fill="none" stroke="#3aa9e1" stroke-width="1.6" stroke-linecap="round" stroke-linejoin="round"/></svg>
    </span>
    <span class="step-button" aria-label="Next step">
      <svg width="18" height="14" viewBox="0 0 18 14"><path d="M1 7h15M11 1.5L16.5 7 11 12.5" fill="none" stroke="#3aa9e1" stroke-width="1.6" stroke-linecap="round" stroke-linejoin="round"/></svg>
    </span>
  </nav>
</main>

<div class="illustration illustration-left" role="img" aria-label="Cartoon boy in a pink shirt resting his foot on an orange ball"></div>
<div class="illustration illustration-right" role="img" aria-label="Cartoon boy in red trousers holding a big swirl lollipop"></div>

<div class="progress" aria-label="Registration progress, step 2">
  <span class="progress-dot" style="left:77px"></span>
  <span class="progress-dot is-current" style="left:141px"></span>
  <span class="progress-dot" style="left:204px"></span>
  <span class="progress-dot" style="left:268px"></span>
  <span class="progress-dot" style="left:331px"></span>
  <span class="progress-dot" style="left:395px"></span>
  <span class="progress-dot" style="left:459px"></span>
  <span class="progress-dot" style="left:522px"></span>
  <span class="progress-dot" style="left:586px"></span>
  <span class="progress-dot" style="left:649px"></span>
  <span class="progress-dot" style="left:713px"></span>
</div>

</body>
</html>
```